WordPress Design for both website and landing page for an expert

I need a clean and stylish design for my new website. I work as an expert (see attached file WHY HOW WHAT), my product is expert opinion (reports) for company evaluations You can use all of the attached pictures colored or black / white. The person is me, you can add other pictures, if you want. The design should be clean and stylish, so you could use white, black, gray, silver and / or one additional color. I have added an idea about my website, see attached file CONCEPT WEBSITE If you have any more information, please do not hesitate to contact us 'Hesitate to ask me ...

```html
<!DOCTYPE html>
<html lang="de">
<head>
<meta charset="utf-8">
<title>Lukas Brenner – Sachverständiger für Firmenbewertungen</title>
<link href="https://fonts.googleapis.com/css2?family=Roboto:wght@400;500;700&family=Open+Sans:wght@400;600&display=swap" rel="stylesheet">
<style>
:root{
  --black:#0d0d0d;
  --ink:#1c1c1c;
  --slate:#5e666d;
  --grey-text:#8a9096;
  --soft:#f2f2f2;
  --line:#e2e2e2;
  --white:#ffffff;
}
*{margin:0;padding:0;box-sizing:border-box}
html,body{width:762px;height:1200px;overflow:hidden;background:var(--white)}
body{position:relative;font-family:"Roboto",sans-serif;color:var(--ink)}

.site-header{position:absolute;left:0;top:0;width:762px;height:58px;background:var(--black)}
.brand{position:absolute;left:77px;top:18px;display:flex;align-items:center;gap:6px;color:var(--white);font-size:11px;letter-spacing:2px;font-weight:400}
.brand-dot{width:8px;height:8px;border-radius:50%;background:var(--white)}
.main-nav{position:absolute;top:22px;left:287px;display:flex;gap:0}
.main-nav a{color:var(--white);text-decoration:none;font-size:11.5px;margin-right:32px}
.main-nav a.active{color:#9a9a9a}

.hero{position:absolute;left:0;top:58px;width:762px;height:380px;
  background:linear-gradient(90deg,#e9ecee 0%,#c9ced1 35%,#9aa1a5 62%,#d7dadb 100%)}
.hero-photo-person{position:absolute;left:380px;top:0;width:260px;height:350px;
  background:linear-gradient(180deg,#c8beb4 0%,#4a4d52 30%,#2d3035 100%);opacity:.85}
.hero-title{position:absolute;left:86px;top:100px;font-size:22.5px;font-weight:700;line-height:28px;color:var(--ink)}
.hero-sub{position:absolute;left:90px;top:160px;width:290px;font-size:11.5px;line-height:16px;color:var(--ink)}
.slider-dots{position:absolute;left:94px;top:279px;display:flex;gap:9px}
.slider-dots span{width:9px;height:9px;border-radius:50%;background:var(--black)}
.slider-dots span.current{background:var(--white)}
.hero-edge{position:absolute;left:0;top:370px}

.card{position:absolute;background:var(--white);box-shadow:0 2px 12px rgba(0,0,0,.12)}
.reasons{left:71px;top:469px;width:215px;height:421px}
.card-head{background:var(--slate);color:var(--white)}
.reasons .card-head{height:99px;padding:12px 19px}
.reasons h2{font-size:20px;font-weight:700;line-height:24px}
.reasons h2 small{display:block;font-size:16px;font-weight:500;line-height:21px}
.reason{position:relative;padding:0 19px}
.reason.alt{background:var(--soft)}
.reason h3{font-size:15px;font-weight:700;position:absolute;left:57px}
.reason p{font-family:"Open Sans",sans-serif;font-size:8.6px;line-height:13px;color:#333;position:absolute;left:19px;width:185px}
.reason svg{position:absolute;left:19px}

.faq{left:310px;top:470px;width:381px;height:372px}
.faq .card-head{height:48px;padding:10px 23px}
.faq h2{font-size:20px;font-weight:700}
.faq-item{display:flex;align-items:center;border-bottom:1px solid var(--line);padding:0 12px 0 18px;font-size:9px;font-weight:500;color:var(--grey-text);line-height:12px}
.faq-item b{width:23px;font-size:11px;font-weight:700;color:#9aa0a5}
.faq-item span{flex:1}
.faq-item.open{color:var(--ink);border-bottom:none}
.faq-answer{background:var(--soft);margin:0 2px;padding:14px 40px 10px 40px;font-family:"Open Sans",sans-serif;font-size:7.2px;line-height:13px;color:#333;height:97px}
.faq-answer p+p{margin-top:8px}
.faq-more{padding:18px 0 0 43px;font-size:11px;color:#555}

.promise{position:absolute;left:0;top:896px;width:762px;height:268px;
  background:radial-gradient(ellipse at 50% 60%,#3a3f44 0%,#23262a 55%,#15171a 100%)}
.promise-edge{position:absolute;left:0;top:0}
.promise h2{position:absolute;top:96px;width:100%;text-align:center;color:var(--white);font-size:22px;font-weight:700}
.promise p{position:absolute;top:134px;left:146px;width:470px;text-align:center;color:var(--white);font-size:11px;line-height:19.5px}
.promise a{position:absolute;left:292px;top:186px;width:178px;height:27px;border:1px solid var(--white);border-radius:14px;color:var(--white);text-decoration:none;font-size:11px;text-align:center;line-height:25px}

.site-footer{position:absolute;left:0;top:1164px;width:762px;height:36px;background:var(--black);color:var(--white);font-size:11px}
.site-footer .legal{position:absolute;width:100%;text-align:center;top:11px}
.site-footer svg{position:absolute;left:672px;top:13px}
</style>
</head>
<body>

<header class="site-header">
  <div class="brand"><span class="brand-dot"></span>LUKAS BRENNER</div>
  <nav class="main-nav">
    <a class="active" href="#">Home</a>
    <a href="#">What I Do</a>
    <a href="#">Why I do it &amp; How I do it</a>
    <a href="#">About Me</a>
    <a href="#">Contact</a>
  </nav>
</header>

<section class="hero" role="img" aria-label="Portrait of the expert in a dark suit standing in a bright modern office corridor">
  <div class="hero-photo-person"></div>
  <h1 class="hero-title">SACHVERSTÄNDIGER FÜR<br>FIRMENBEWERTUNGEN</h1>
  <p class="hero-sub">Sie benötigen ein Gutachten zur Ermittlung des Wertes Ihres Unternehmens</p>
  <div class="slider-dots"><span></span><span class="current"></span><span></span></div>
  <svg class="hero-edge" width="762" height="70" viewBox="0 370 762 70">
    <polygon points="0,376 272,390 0,437" fill="#0d0d0d"/>
    <polygon points="0,437 272,390 762,412 762,440 0,440" fill="#fff"/>
  </svg>
</section>

<section class="card reasons">
  <div class="card-head"><h2>3 Reasons<small>why you should work with me</small></h2></div>
  <div class="reason" style="height:106px">
    <svg width="30" height="30" viewBox="0 0 30 30" style="top:16px" fill="none" stroke="#222" stroke-width="1.2"><path d="M2 18 L28 3 L20 26 L14 19 Z M28 3 L14 19 L13 26 L17 21"/></svg>
    <h3 style="top:23px">Schnell</h3>
    <p style="top:52px">Sie bekommen Ihr Gutachten zeitnah (innerhalb von max. 21 Tagen nach Zugang aller benötigten Unterlagen)</p>
  </div>
  <div class="reason alt" style="height:102px">
    <svg width="30" height="30" viewBox="0 0 30 30" style="top:8px" fill="none" stroke="#222" stroke-width="1.2"><path d="M15 1 L18 4 L22 3 L23 7 L27 9 L25 13 L28 16 L25 19 L26 23 L22 24 L20 28 L16 26 L12 28 L10 24 L5 23 L6 19 L2 15 L5 12 L4 8 L8 7 L10 3 L13 4 Z"/><path d="M9 15 L13 19 L21 11" stroke-width="1.8"/></svg>
    <h3 style="top:14px">Zertifiziert</h3>
    <p style="top:44px">Sie erhalten ein qualifiziertes und belastbares Gutachten von einem zertifizierten Sachverständigen (höchste Akzeptanz bei allen Parteien)</p>
  </div>
  <div class="reason" style="height:114px">
    <svg width="30" height="36" viewBox="0 0 30 36" style="top:8px" fill="none" stroke="#222" stroke-width="1.2"><path d="M4 2 H20 L26 8 V34 H4 Z M20 2 V8 H26"/><path d="M8 14 H22 M8 18 H22 M8 22 H22 M8 26 H22 M8 30 H18"/></svg>
    <h3 style="top:18px">Verständlich</h3>
    <p style="top:54px">Ihr Gutachten wird für Sie logisch und nachvollziehbar sein und kein "Fachchinesisch" enthalten</p>
  </div>
</section>

<section class="card faq">
  <div class="card-head"><h2>FAQ</h2></div>
  <div class="faq-item" style="height:37px"><b>Q.</b><span>What are the buying motives of the customers?</span></div>
  <div class="faq-item" style="height:33px"><b>Q.</b><span>Was sind die Kaufmotive der Kunden?</span></div>
  <div class="faq-item" style="height:33px"><b>Q.</b><span>Sie wollen Anteile Ihres Unternehmens oder ihr gesamtes Unternehmen verkaufen?</span></div>
  <div class="faq-item" style="height:39px"><b>Q.</b><span>Sie wollen Ihr Unternehmen auf Ihre Erben übertragen und benötigen eine Bewertung für das Finanzamt?</span></div>
  <div class="faq-item open" style="height:38px"><b>Q.</b><span>Sie müssen im Rahmen einer Trennung/Scheidung jemanden ausbezahlen und benötigen eine Bemessungsgrundlage?</span></div>
  <div class="faq-answer">
    <p>Lassen Sie Ihr Unternehmen von einem qualifizierten Sachverständigen bewerten und gehen somit vielen (unnötigen) Streitereien aus dem Weg.</p>
    <p>Merke: Die Kosten für ein Gutachten sind immer überproportional günstiger als die Kosten für Rechtsstreitigkeiten. Und das losgelöst von der psychischen Belastung einer solchen Auseinandersetzung ...</p>
  </div>
  <div class="faq-more">View More FAQ &nbsp;<svg width="6" height="8" viewBox="0 0 6 8"><path d="M1 1 L4.5 4 L1 7" stroke="#555" stroke-width="1.5" fill="none"/></svg></div>
</section>

<section class="promise" role="img" aria-label="Dimmed photo of a business meeting with charts and documents on a table">
  <svg class="promise-edge" width="762" height="50" viewBox="0 0 762 50">
    <polygon points="0,0 762,0 762,4 532,44 0,28" fill="#fff"/>
    <polygon points="532,44 762,0 762,44" fill="#0d0d0d"/>
  </svg>
  <h2>Mein Qualitätsversprechen</h2>
  <p>Sollte der avisierte Termin für die Erstellung des Gutachtens überschritten werden, erhalten Sie das Gutachten absolut kostenfrei!</p>
  <a href="#">Ich verzichte auf mein Honorar</a>
</section>

<footer class="site-footer">
  <div class="legal">© 2018 &nbsp;|&nbsp; www.brenner-gutachten.de</div>
  <svg width="10" height="8" viewBox="0 0 10 8"><path d="M1 6 L5 2 L9 6" stroke="#fff" stroke-width="2" fill="none"/></svg>
</footer>

</body>
</html>
```